Advertising company unique advertising platform

we need a logo design for a new company based in Australia Melbourne. We develop innovated advertising platform where consumer can use this platform to get regular discount, as business owner they can use this platform for free advertisement. Payment for this advertisement platform only payable every two weeks, when I generate revenue for their business

Industry/Entity Type

Advertising

Contact Information for Business Card

Dale Morven | Co-Founder |Managing Director
Suite 718 240 Wattlebrook Lane Melbourne Vic 3000

ABN 38 614 207 923
Tel: +61 0487 259 318 | Email: dale.morven@plivorantu.com

Font styles to use
Decorative
Script

Requirements
Must have
• Try few different design and some round corner business card
Should not have
• One round corner business card...try 4 different colour background not only black, make sure two side is designed. Be creative so imagine you are giving this to a client make sure has wow factor, if you can also try one design with engrave like all the logo, words look 3d feel
• The word Advertising Platform use attached file font

```html
<!DOCTYPE html>
<html lang="en">
<head>
<meta charset="utf-8">
<title>Kestrava Point – Business Card</title>
<link rel="stylesheet" href="https://fonts.googleapis.com/css2?family=Roboto:wght@400;500;700;900&display=swap">
<style>
  :root {
    --canvas: #e9e6e2;
    --card-dark: #262626;
    --card-dark-edge: #1b1b1b;
    --glow-yellow: #f7c948;
    --glow-orange: #f08a2c;
    --edge-red: #e2462a;
    --ink: #1d1d1d;
    --text-light: #f2f2f2;
    --accent: #f26a2a;
    --band-start: #ef4f24;
    --band-end: #f7a23a;
  }
  * { box-sizing: border-box; margin: 0; padding: 0; }
  html, body {
    width: 1200px; height: 886px; overflow: hidden;
    background: var(--canvas);
    font-family: "Roboto", Arial, sans-serif;
  }
  .stage { position: relative; width: 1200px; height: 886px; }

  .card {
    position: absolute;
    width: 620px; height: 354px;
    border-radius: 26px;
    overflow: hidden;
    box-shadow: 0 14px 30px rgba(0,0,0,.22);
  }

  /* Front */
  .card--front { left: 60px; top: 60px; }
  .front-pattern {
    position: absolute; inset: 0;
    background: radial-gradient(ellipse at 50% 45%, var(--glow-yellow) 0%, var(--glow-orange) 48%, var(--edge-red) 100%);
  }
  .front-brand {
    position: absolute; left: 0; right: 0; top: 128px;
    text-align: center;
  }
  .front-brand__name {
    font-weight: 900; font-size: 58px; letter-spacing: 1px;
    color: var(--ink); line-height: 1;
  }
  .front-brand__web {
    margin-top: 16px;
    font-weight: 500; font-size: 15px; letter-spacing: 5px;
    color: var(--ink);
  }

  /* Back */
  .card--back {
    left: 520px; top: 470px;
    background: linear-gradient(160deg, var(--card-dark) 0%, var(--card-dark-edge) 100%);
  }
  .back-brand {
    position: absolute; left: 44px; top: 34px;
    display: flex; align-items: center; gap: 12px;
  }
  .back-brand__dot {
    width: 34px; height: 34px; border-radius: 50%;
    background: var(--accent);
  }
  .back-brand__name {
    font-weight: 900; font-size: 32px; color: var(--accent); line-height: 1;
  }
  .contact {
    position: absolute; left: 44px; top: 104px;
    width: 240px;
    color: var(--text-light); font-size: 15px; line-height: 20px;
  }
  .contact__group { margin-bottom: 10px; }
  .contact__row { display: flex; align-items: center; gap: 9px; white-space: nowrap; }
  .contact__icon { width: 13px; height: 13px; flex: none; }

  .title-band {
    position: absolute; right: 0; top: 236px;
    width: 300px; height: 82px;
    background: linear-gradient(90deg, var(--band-start) 0%, var(--band-end) 100%);
    text-align: right; padding: 10px 24px 0 0;
    color: var(--ink); text-transform: uppercase;
  }
  .title-band__name { font-weight: 700; font-size: 23px; line-height: 26px; }
  .title-band__role { font-weight: 500; font-size: 16px; line-height: 20px; }
  .title-mark {
    position: absolute; left: 288px; top: 212px;
    width: 64px; height: 64px; border-radius: 50%;
    background: var(--accent);
  }
</style>
</head>
<body>
<main class="stage">

  <section class="card card--front">
    <div class="front-pattern" role="img" aria-label="Warm yellow-to-orange background with a faint repeating flame pattern"></div>
    <div class="front-brand">
      <div class="front-brand__name">Kestrava Point</div>
      <div class="front-brand__web">www.plivorantu.com</div>
    </div>
  </section>

  <section class="card card--back">
    <div class="back-brand">
      <span class="back-brand__dot"></span>
      <span class="back-brand__name">Kestrava Point</span>
    </div>

    <div class="contact">
      <div class="contact__group">
        <div>Plivorantu</div>
        <div>ABN 38 614 207 923</div>
      </div>
      <div class="contact__group">
        <div>Suite 718 240 Wattlebrook Lane</div>
        <div>Melbourne Vic 3000</div>
      </div>
      <div class="contact__row">
        <svg class="contact__icon" viewBox="0 0 24 24" aria-hidden="true"><path fill="#f26a2a" d="M6.6 10.8a15.1 15.1 0 0 0 6.6 6.6l2.2-2.2a1 1 0 0 1 1-.25 11.4 11.4 0 0 0 3.6.57 1 1 0 0 1 1 1V20a1 1 0 0 1-1 1A17 17 0 0 1 3 4a1 1 0 0 1 1-1h3.5a1 1 0 0 1 1 1c0 1.250.2 2.450.57 3.570a1 1 0 0 1-.25 1z"/></svg>
        <span>+61 0487 259 318</span>
      </div>
      <div class="contact__row">
        <svg class="contact__icon" viewBox="0 0 24 24" aria-hidden="true"><rect x="2" y="5" width="20" height="14" rx="2" fill="#f26a2a"/><path d="M3 6l9 7 9-7" fill="none" stroke="#262626" stroke-width="2"/></svg>
        <span>dale.morven@plivorantu.com</span>
      </div>
    </div>

    <div class="title-band">
      <div class="title-band__name">Dale Morven</div>
      <div class="title-band__role">Co-Founder</div>
      <div class="title-band__role">Managing Director</div>
    </div>
    <span class="title-mark"></span>
  </section>

</main>
</body>
</html>
```